Wellpath Ledgers New Website

Please review the attached Design Brief with additional details. Thank you!

The goal is to create a website that effectively communicates the benefits of WellPath Ledgers to eye care professionals. The website should streamline the process of understanding and utilizing WellPath Ledgers' services, emphasizing improved patient outcomes, increased referrals, and enhanced patient engagement.

Target Market(s)

Eyecare Professionals

Number of Pages Required

4 page

```html
<!DOCTYPE html>
<html lang="en">
<head>
<meta charset="utf-8">
<title>Wellpath Ledgers</title>
<link href="https://fonts.googleapis.com/css2?family=Kanit:wght@300;400;500&family=Poppins:wght@400;500&display=swap" rel="stylesheet">
<style>
:root{
  --blue:#1b2a9c;
  --blue-link:#2a6fd6;
  --orange:#f6a531;
  --ink:#2b2b2b;
  --muted:#4a4a4a;
  --line:#bdbdbd;
  --white:#ffffff;
  --black:#000000;
}
*{box-sizing:border-box;margin:0;padding:0}
html,body{width:1200px;height:3976px;overflow:hidden;background:var(--white)}
body{font-family:"Kanit",sans-serif;color:var(--ink)}
.page{position:relative;width:1200px;height:3976px;overflow:hidden}
.abs{position:absolute}
.btn{position:absolute;display:flex;align-items:center;justify-content:center;background:var(--blue);color:var(--white);border-radius:30px;font-family:"Kanit",sans-serif;font-weight:400;font-size:19px}
.accent{color:var(--orange)}
.rule{position:absolute;height:3px;background:var(--orange)}
.body-text{font-family:"Poppins",sans-serif;font-size:14.5px;line-height:32px;color:var(--muted)}

/* header */
.logo-box{left:111px;top:0;width:253px;height:111px;background:var(--white);box-shadow:0 3px 12px rgba(0,0,0,.12);border-radius:0 0 6px 6px;display:flex;align-items:center;justify-content:center;gap:10px;z-index:3}
.logo-dot{width:18px;height:18px;border-radius:50%;background:var(--orange)}
.logo-name{font-family:"Kanit",sans-serif;font-weight:400;font-size:25px;color:var(--blue)}
.nav{left:408px;top:30px;display:flex;gap:30px;font-size:14.5px;color:var(--ink);z-index:3}
.nav .active{color:var(--blue-link);border-bottom:2px solid var(--blue-link);padding-bottom:6px}

/* hero */
.hero-card{left:568px;top:120px;width:549px;height:354px;background:var(--white);border-radius:8px;text-align:center;z-index:2}
.hero-card h1{font-weight:400;font-size:34px;margin-top:104px;color:var(--ink)}
.hero-card p{font-size:21px;line-height:36px;margin-top:10px;color:var(--ink)}

/* about */
.h2{position:absolute;font-family:"Kanit",sans-serif;font-weight:400;font-size:38px;color:var(--blue)}
.about-lead{left:111px;top:856px;width:490px;font-family:"Kanit",sans-serif;font-weight:300;font-size:19px;line-height:36px;color:var(--ink)}
.about-copy{left:673px;top:782px;width:420px}
.photo{position:absolute}
.badge{left:526px;top:1091px;width:72px;height:72px;border-radius:50%;background:var(--white);box-shadow:0 2px 10px rgba(0,0,0,.15)}

/* services */
.services{left:0;top:1569px;width:1200px;height:340px;display:flex}
.tile{position:relative;width:300px;height:340px;color:var(--white);font-weight:500;font-size:22px;line-height:35px}
.tile svg{position:absolute;left:22px;top:165px}
.tile span{position:absolute;left:22px;top:249px;width:260px}
.tile.orange{background:linear-gradient(135deg,#e9b067,#d98e33)}
.tile.blue{background:linear-gradient(135deg,#4150c0,#2533a8)}
.dots{left:542px;top:1951px;display:flex;gap:7px}
.dots i{display:block;width:34px;height:4px;border-radius:2px;background:#5b6bd0}
.dots i:first-child{background:var(--blue)}

/* pricing */
.price-list{left:110px;top:2155px;width:370px;list-style:none}
.price-list li{position:relative;padding-left:31px}
.price-list li::before{content:"→";position:absolute;left:0;top:0;color:var(--ink);font-size:14px}
.price-card{position:absolute;top:2049px;width:272px;height:278px;border:1px solid #e2e2e2;border-radius:8px;box-shadow:0 2px 10px rgba(0,0,0,.1);text-align:center;background:var(--white)}
.price-card h3{font-weight:400;font-size:19px;color:var(--blue);margin-top:34px}
.price-card .amount{font-size:28px;color:var(--ink);margin-top:12px}
.price-card p{font-family:"Poppins",sans-serif;font-size:14px;line-height:28px;color:var(--muted);margin-top:8px}
.price-card .btn{left:62px;top:200px;width:148px;height:48px}

/* benefits */
.benefits-band{left:0;top:2420px;width:1200px;height:514px;overflow:hidden}
.benefits-title{left:70px;top:2570px;width:468px;text-align:center;font-size:32px;color:var(--white)}
.benefit-list{left:120px;top:2660px;width:380px;list-style:none;font-family:"Poppins",sans-serif;font-size:14.5px;line-height:33px;color:var(--white)}
.benefit-list li{position:relative;padding-left:33px}
.benefit-list svg{position:absolute;left:0;top:8px}

/* testimonial & contact */
.quote{left:111px;top:3252px;width:490px}
.author{left:111px;top:3397px;font-size:20px;color:var(--blue)}
.author-place{left:111px;top:3437px;font-family:"Poppins",sans-serif;font-size:14.5px;color:var(--muted)}
.contact-card{left:622px;top:3025px;width:464px;height:458px;border:1px solid #e2e2e2;border-radius:6px;box-shadow:0 2px 12px rgba(0,0,0,.1);background:var(--white)}
.field{position:absolute;left:36px;width:394px;border-bottom:1px solid #555;font-family:"Poppins",sans-serif;font-size:14px;color:#444;padding-bottom:7px}

/* footer */
.foot-h{position:absolute;top:3692px;font-size:20px;color:var(--white)}
.foot-col{position:absolute;top:3750px;list-style:none;font-family:"Poppins",sans-serif;font-size:15px;line-height:35.5px;color:var(--white)}
.foot-logo{left:111px;top:3768px;display:flex;align-items:center;gap:10px}
.foot-logo .logo-name{color:var(--white);font-size:28px}
.foot-rule{left:111px;top:3920px;width:978px;height:1px;background:#555}
.copyright{left:0;top:3936px;width:1200px;text-align:center;font-family:"Poppins",sans-serif;font-size:14px;color:var(--white)}
</style>
</head>
<body>
<div class="page">

  <svg class="abs" style="left:0;top:0" width="1200" height="720" viewBox="0 0 1200 720">
    <defs>
      <linearGradient id="heroTone" x1="0" y1="0" x2="1" y2="1">
        <stop offset="0" stop-color="#d9e3ea"/>
        <stop offset=".45" stop-color="#a8b7c2"/>
        <stop offset="1" stop-color="#6d5a57"/>
      </linearGradient>
    </defs>
    <path role="img" aria-label="Photo of a doctor with a stethoscope tapping a tablet" d="M0 87 H1200 V556 Q640 760 0 556 Z" fill="url(#heroTone)"/>
  </svg>

  <div class="abs logo-box"><span class="logo-dot"></span><span class="logo-name">Wellpath Ledgers</span></div>
  <nav class="abs nav">
    <span class="active">Home</span><span>About Us</span><span>Services</span><span>Pricing</span><span>Testimonials</span><span>Blog/News</span><span>Contact Us</span><span>FAQs</span>
  </nav>

  <div class="abs hero-card">
    <h1>Clinically Actionable Analytics</h1>
    <p>Track, Measure and Compare Your<br>Clinical Outcomes</p>
    <div class="btn" style="left:204px;top:249px;width:138px;height:45px;font-size:18px">Get Started</div>
  </div>

  <h2 class="h2" style="left:111px;top:780px">About <span class="accent">Us</span></h2>
  <div class="rule" style="left:111px;top:833px;width:66px"></div>
  <p class="abs about-lead">The eye care industry’s leading software designed to extract and analyze clinical outcomes from your EHR.</p>
  <p class="abs about-copy body-text">Sed ut perspiciatis unde omnis iste natus error sit voluptatem accusantium doloremque laudantium, totam rem aperiam, eaque ipsa quae ab illo inventore veritatis et quasi architecto beatae vitae dicta sunt explicabo. Nemo enim ipsam voluptatem quia voluptas sit aspernatur aut odit aut fugit, sed quia consequuntur magni dolores eos qui ratione voluptatem sequi nesciunt.</p>
  <div class="btn" style="left:673px;top:1033px;width:148px;height:48px">Learn More</div>
  <div class="photo" role="img" aria-label="Photo of two women reviewing paperwork at a table" style="left:111px;top:973px;width:470px;height:287px;background:linear-gradient(135deg,#c9b9a6,#8a7666 55%,#d8d2c8)"></div>
  <div class="photo" role="img" aria-label="Photo of a nurse in scrubs holding a tablet in a bright corridor" style="left:542px;top:1114px;width:547px;height:259px;background:linear-gradient(90deg,#e6e9ee,#cfd6de 45%,#3f8f93 70%,#dfe3e8)"></div>
  <div class="abs badge"></div>

  <h2 class="h2" style="left:0;top:1452px;width:1200px;text-align:center">Our <span class="accent">Services</span></h2>
  <div class="rule" style="left:565px;top:1508px;width:70px"></div>
  <div class="abs services">
    <div class="tile orange" role="img" aria-label="Diabetes management registry, warm photo background">
      <svg width="64" height="64" viewBox="0 0 64 64" fill="none" stroke="#fff" stroke-width="2.5"><rect x="30" y="4" width="22" height="32" rx="3"/><path d="M35 12h12M35 20h12M35 28h6"/><path d="M4 60V40h10l10-8 8 4-8 10h-6v14"/></svg>
      <span>Diabetes Management Registry</span>
    </div>
    <div class="tile blue" role="img" aria-label="Cataract extraction registry, blue photo background">
      <svg width="72" height="64" viewBox="0 0 72 64" fill="none" stroke="#fff" stroke-width="2.5"><path d="M4 40 Q30 14 58 40 Q30 66 4 40 Z"/><circle cx="31" cy="40" r="9"/><path d="M40 30 L64 6"/><circle cx="64" cy="6" r="3"/></svg>
      <span>Cataract Extraction Registry</span>
    </div>
    <div class="tile orange" role="img" aria-label="Dry eye registry, warm photo background">
      <svg width="72" height="64" viewBox="0 0 72 64" fill="none" stroke="#fff" stroke-width="2.5"><path d="M4 30 Q36 0 68 30 Q36 60 4 30 Z"/><circle cx="36" cy="30" r="11"/><circle cx="36" cy="30" r="4"/><path d="M36 50v10"/></svg>
      <span>Dry Eye Registry</span>
    </div>
    <div class="tile blue" role="img" aria-label="Myopia registry, blue photo background">
      <svg width="80" height="64" viewBox="0 0 80 64" fill="none" stroke="#fff" stroke-width="2.5"><circle cx="34" cy="34" r="26"/><path d="M14 34h60"/><circle cx="58" cy="34" r="10"/></svg>
      <span>Myopia Registry</span>
    </div>
  </div>
  <div class="abs dots"><i></i><i></i><i></i></div>

  <h2 class="h2" style="left:110px;top:2066px">Our <span class="accent">Pricing</span></h2>
  <div class="rule" style="left:110px;top:2124px;width:70px"></div>
  <ul class="abs price-list body-text">
    <li>A subscription entitles subscriber to all WellPath Ledgers data except that which is proprietary.</li>
    <li>Credit card processing fee may apply</li>
  </ul>
  <div class="price-card" style="left:525px">
    <h3>Initial One-Time Setup</h3>
    <div class="amount">1,000 US$</div>
    <p>Lorem ipsum dolor sit amet,<br>consectetur adipiscing elit, sed</p>
    <div class="btn">View Details</div>
  </div>
  <div class="price-card" style="left:815px">
    <h3>Monthly Subscription</h3>
    <div class="amount">99 US$</div>
    <p>Lorem ipsum dolor sit amet,<br>consectetur adipiscing elit, sed</p>
    <div class="btn">View Details</div>
  </div>

  <div class="abs benefits-band">
    <svg width="1200" height="514" viewBox="0 0 1200 514">
      <defs>
        <linearGradient id="labTone" x1="0" y1="0" x2="1" y2="0">
          <stop offset="0" stop-color="#c9d8e3"/>
          <stop offset=".55" stop-color="#dfe6ec"/>
          <stop offset=".75" stop-color="#e9ecef"/>
          <stop offset="1" stop-color="#b8c6d1"/>
        </linearGradient>
      </defs>
      <rect role="img" aria-label="Photo of a doctor in a lab coat working at a laptop" width="1200" height="514" fill="url(#labTone)"/>
      <circle cx="304" cy="314" r="242" fill="none" stroke="var(--blue)" stroke-width="3"/>
      <circle cx="304" cy="314" r="232" fill="var(--blue)"/>
    </svg>
  </div>
  <div class="abs benefits-title">Benefits</div>
  <div class="rule" style="left:270px;top:2621px;width:70px;background:var(--white)"></div>
  <ul class="abs benefit-list">
    <li><svg width="16" height="16" viewBox="0 0 16 16"><circle cx="8" cy="8" r="8" fill="#fff"/><path d="M4.5 8.2l2.3 2.3 4.7-4.8" fill="none" stroke="var(--blue)" stroke-width="1.8"/></svg>Sed ut perspiciatis unde omnis iste natus error sit voluptatem accusantium</li>
    <li><svg width="16" height="16" viewBox="0 0 16 16"><circle cx="8" cy="8" r="8" fill="#fff"/><path d="M4.5 8.2l2.3 2.3 4.7-4.8" fill="none" stroke="var(--blue)" stroke-width="1.8"/></svg>Doloremque laudantium, totam rem aperiam, eaque ipsa quae ab illo inventore</li>
  </ul>
  <div class="btn" style="left:225px;top:2828px;width:156px;height:48px;background:var(--white);color:var(--blue)">View Benefits</div>

  <h2 class="h2" style="left:111px;top:3033px;font-size:32px">Testimonial</h2>
  <div class="rule" style="left:111px;top:3083px;width:70px;background:var(--blue)"></div>
  <div class="abs" role="img" aria-label="Portrait photo of the reviewing optometrist" style="left:111px;top:3124px;width:102px;height:102px;border-radius:50%;background:linear-gradient(135deg,#cfd3d8,#6b6f78)"></div>
  <p class="abs quote body-text">Working with WellPath Ledgers is the best investment that I have ever made in my practices. Access to my clinical outcome data help build pcp referrals. Actually, in one day, I received 40 new diabetic referrals.</p>
  <div class="abs author">- Dr. Marcus Hale OD</div>
  <div class="abs author-place">( Ridgeview Eye Clinic, Brookhaven, Tennessee )</div>

  <div class="abs contact-card">
    <h2 class="h2" style="left:0;top:40px;width:464px;text-align:center;font-size:34px">Contact <span class="accent">Us</span></h2>
    <div class="rule" style="left:200px;top:84px;width:56px"></div>
    <div class="field" style="top:132px">Your Full Name</div>
    <div class="field" style="top:201px">Email Address or Phone Number</div>
    <div class="field" style="top:268px;padding-bottom:30px">Type Your Message</div>
    <div class="btn" style="left:150px;top:365px;width:165px;height:48px">Send Message</div>
  </div>

  <svg class="abs" style="left:0;top:3500px" width="1200" height="476" viewBox="0 0 1200 476">
    <path d="M0 206 Q600 60 1200 200 V476 H0 Z" fill="var(--black)"/>
  </svg>
  <div class="abs foot-logo"><span class="logo-dot"></span><span class="logo-name">Wellpath Ledgers</span></div>
  <div class="foot-h" style="left:443px">Quick Links</div>
  <ul class="foot-col" style="left:443px"><li>Home</li><li>About Us</li><li>Services</li><li>Pricing</li></ul>
  <ul class="foot-col" style="left:582px"><li>Testimonials</li><li>Blog/News</li><li>Contact Us</li><li>FAQs</li></ul>
  <div class="foot-h" style="left:794px">Contact Us</div>
  <ul class="foot-col" style="left:794px"><li>844-555-0142</li><li>ContactUs@WellPathLedgers.com</li><li>98, Lorem Lipsum Sit Amet\092 871</li></ul>
  <div class="abs foot-rule"></div>
  <div class="abs copyright">©2023 Copyrights. All Rights Reserved.</div>

</div>
</body>
</html>
```